BOLD & MINIMALIST DESIGN NEEDED

We want a very bold but minimalistic business card design that is impactful and utilizes both sides of the business card. Our current logo is included for your use.

We want bold fonts and good use of negative space. We don't want the logo to overpower the design.

Target Market(s)

Professionals who are building new commercial buildings.

Industry/Entity Type

Construction

Contact Information for Business Card

Name, Title, email, office phone, cell phone, website

Font styles to use
Serif
Sans Serif

Requirements
Must have
• Bold design!

```html
<!DOCTYPE html>
<html lang="en">
<head>
<meta charset="utf-8">
<title>Summitline Design + Build — Business Card</title>
<link rel="stylesheet" href="https://fonts.googleapis.com/css2?family=Montserrat:wght@400;500;700&display=swap">
<style>
  :root {
    --backdrop: #dcdcdc;
    --paper: #ffffff;
    --ink: #0c0d0f;
    --white: #ffffff;
    --accent: #8dc63f;
  }
  * { margin: 0; padding: 0; box-sizing: border-box; }
  html, body {
    width: 1200px; height: 1200px; overflow: hidden;
    background: var(--backdrop);
    font-family: "Montserrat", Arial, sans-serif;
  }
  .canvas { position: relative; width: 1200px; height: 1200px; }
  .card {
    position: absolute; left: 179px; width: 861px; height: 496px; overflow: hidden;
  }
  .card--front { top: 84px; background: var(--paper); }
  .card--back  { top: 622px; background: var(--ink); }

  .brand {
    position: absolute; display: flex; align-items: center; gap: 14px;
    font-weight: 700; white-space: nowrap; letter-spacing: 0.05em;
  }
  .brand__mark { flex: none; }
  .brand__name { display: flex; flex-direction: column; }
  .card--front .brand {
    left: 0; right: 0; top: 0; bottom: 0; justify-content: center;
    font-size: 34px; line-height: 44px; color: var(--ink);
  }
  .card--front .brand__mark { width: 20px; height: 20px; background: var(--ink); }
  .card--back .brand {
    left: 96px; top: 215px;
    font-size: 24px; line-height: 32px; color: var(--white);
  }
  .card--back .brand__mark { width: 16px; height: 16px; background: var(--white); }

  .divider {
    position: absolute; left: 414px; top: 144px; width: 2px; height: 205px;
    background: linear-gradient(var(--accent) 0 60px, #b8b8b8 60px);
  }
  .person { position: absolute; left: 433px; top: 140px; }
  .person__name {
    font-size: 34px; font-weight: 700; color: var(--white); line-height: 40px;
    letter-spacing: 0.01em;
  }
  .person__title {
    font-size: 28px; font-weight: 500; color: var(--accent); line-height: 34px;
    letter-spacing: 0.02em;
  }
  .contacts {
    position: absolute; left: 433px; top: 225px; list-style: none;
  }
  .contacts li {
    display: flex; align-items: center; height: 35px;
    font-size: 23px; color: var(--white); letter-spacing: 0.03em;
  }
  .contacts svg { width: 22px; height: 22px; margin-right: 18px; flex: none; }
  .contacts .hl { color: var(--accent); }
</style>
</head>
<body>
<div class="canvas">
  <section class="card card--front">
    <div class="brand">
      <span class="brand__mark"></span>
      <span class="brand__name"><span>SUMMITLINE</span><span>DESIGN + BUILD</span></span>
    </div>
  </section>

  <section class="card card--back">
    <div class="brand">
      <span class="brand__mark"></span>
      <span class="brand__name"><span>SUMMITLINE</span><span>DESIGN + BUILD</span></span>
    </div>
    <div class="divider"></div>
    <div class="person">
      <p class="person__name">Name Surename</p>
      <p class="person__title">Director</p>
    </div>
    <ul class="contacts">
      <li>
        <svg viewBox="0 0 24 24" fill="none" stroke="var(--accent)" stroke-width="2" stroke-linecap="round" stroke-linejoin="round"><path d="M5 3h4l2 5-3 2a11 11 0 0 0 6 6l2-3 5 2v4a2 2 0 0 1-2 2A17 17 0 0 1 3 5a2 2 0 0 1 2-2z"/><path d="M15 3a6 6 0 0 1 6 6M15 7a2 2 0 0 1 2 2"/></svg>
        555-014-2200
      </li>
      <li>
        <svg viewBox="0 0 24 24" fill="var(--accent)"><path d="M2 8c0-3 20-3 20 0v2h-5V8H7v2H2z"/><path d="M6 11h12l3 10H3z"/><circle cx="12" cy="16" r="2.5" fill="var(--ink)"/></svg>
        555-014-2200
      </li>
      <li>
        <svg viewBox="0 0 24 24" fill="none" stroke="var(--accent)" stroke-width="2"><rect x="2" y="5" width="20" height="14"/><path d="M2 5l10 8 10-8M2 19l8-7M22 19l-8-7"/></svg>
        info@s-d-b.com
      </li>
      <li>
        <svg viewBox="0 0 24 24" fill="none" stroke="var(--accent)" stroke-width="1.8"><circle cx="12" cy="12" r="10"/><ellipse cx="12" cy="12" rx="4.5" ry="10"/><path d="M2 12h20M4 7h16M4 17h16"/></svg>
        www.<span class="hl">s-d-b</span>.com
      </li>
    </ul>
  </section>
</div>
</body>
</html>
```